Business Card for a Creative Technology based HR services company

Our company name is Lumo8, and we build large communities of HR (human resource) and finance personnels through our mobile platform, and we conduct lots of on-line and off-line activities to get everyone constantly connected. Behind all these, we will also provide on-site HR and finance contractors to our clients, plus a host of other HR-related services. No process in our company takes more than 5-steps.
Our company slogan: Shaping Your Career
Target Market(s)
All human resource (HR) and finance personnels, from new entrants to highly experienced senior professionals.
Industry/Entity Type
Finance
Colors
Designer to choose colors to be used in the design.
Look and feel
Each slider illustrates characteristics of the customer's brand and the style your logo design should communicate.

```html
<!DOCTYPE html>
<html lang="en">
<head>
<meta charset="utf-8">
<title>Lumo8 Business Card</title>
<link href="https://fonts.googleapis.com/css2?family=Jost:wght@400;600&family=Cinzel:wght@400&display=swap" rel="stylesheet">
<style>
  :root {
    --navy: #14295a;
    --red: #e0141e;
    --paper: #f3f3f3;
    --ink: #3a3a3a;
    --rule: #9a9a9a;
    --backdrop: #e4e4e2;
  }
  html, body {
    margin: 0;
    width: 1200px;
    height: 900px;
    overflow: hidden;
    background: var(--backdrop);
    font-family: "Jost", sans-serif;
  }
  .card {
    position: absolute;
    left: 285px;
    width: 630px;
    height: 360px;
    background: var(--paper);
    box-shadow: 0 4px 14px rgba(0,0,0,0.12);
    overflow: hidden;
  }
  .card--back { top: 60px; }
  .card--front { top: 480px; }

  .wordmark {
    display: flex;
    align-items: center;
    gap: 8px;
    color: var(--navy);
    font-weight: 600;
    letter-spacing: 0.5px;
  }
  .wordmark__dot {
    background: var(--red);
    border-radius: 50%;
  }

  .card--back .wordmark {
    position: absolute;
    left: 200px;
    top: 120px;
    font-size: 64px;
    line-height: 1;
  }
  .card--back .wordmark__dot { width: 34px; height: 34px; }
  .tagline {
    position: absolute;
    left: 204px;
    top: 206px;
    font-family: "Cinzel", serif;
    font-size: 11px;
    letter-spacing: 2px;
    color: var(--navy);
  }

  .card--front .wordmark {
    position: absolute;
    left: 150px;
    top: 42px;
    font-size: 44px;
    line-height: 1;
  }
  .card--front .wordmark__dot { width: 24px; height: 24px; }
  .divider {
    position: absolute;
    left: 0;
    top: 118px;
    width: 520px;
    height: 1px;
    background: var(--rule);
  }
  .address {
    position: absolute;
    left: 78px;
    top: 150px;
    font-size: 12px;
    line-height: 22px;
    letter-spacing: 1.6px;
    text-transform: uppercase;
    color: var(--ink);
  }
  .person {
    position: absolute;
    right: 40px;
    top: 150px;
    text-align: right;
  }
  .person__name {
    font-family: "Cinzel", serif;
    font-size: 19px;
    letter-spacing: 3px;
    color: var(--ink);
  }
  .person__title {
    display: inline-block;
    margin-top: 4px;
    padding-left: 60px;
    border-top: 1px solid var(--rule);
    font-family: "Cinzel", serif;
    font-size: 13px;
    letter-spacing: 2px;
    color: var(--navy);
  }
  .contacts {
    position: absolute;
    right: 40px;
    top: 212px;
    margin: 0;
    padding: 0;
    list-style: none;
  }
  .contacts li {
    display: flex;
    justify-content: flex-end;
    align-items: center;
    gap: 12px;
    height: 22px;
    font-size: 13px;
    letter-spacing: 1.4px;
    color: var(--ink);
  }
  .contacts svg { width: 14px; height: 14px; }
  .footer-band {
    position: absolute;
    left: 0;
    bottom: 0;
    width: 630px;
    height: 46px;
  }
  .website {
    position: absolute;
    left: 30px;
    bottom: 13px;
    font-size: 13px;
    letter-spacing: 3px;
    color: #ffffff;
  }
</style>
</head>
<body>

<section class="card card--back" aria-label="Card back">
  <div class="wordmark"><span>Lumo8</span><span class="wordmark__dot"></span></div>
  <div class="tagline">Shaping Your Career</div>
</section>

<section class="card card--front" aria-label="Card front">
  <div class="wordmark"><span>Lumo8</span><span class="wordmark__dot"></span></div>
  <div class="divider"></div>

  <div class="address">
    2180 Alder Lane, Suite #4<br>
    Fairbrook, CA 95010
  </div>

  <div class="person">
    <div class="person__name">Dana Whitfield</div>
    <div class="person__title">CEO</div>
  </div>

  <ul class="contacts">
    <li>555-204-1180
      <svg viewBox="0 0 14 14" fill="none" stroke="#e0141e" stroke-width="1.3"><path d="M2 5c0-2 2-3 5-3s5 1 5 3l-2 1-1-2H5L4 6z"/><rect x="3" y="7" width="8" height="5" rx="1"/></svg>
    </li>
    <li>555-317-6420
      <svg viewBox="0 0 14 14" fill="none" stroke="#e0141e" stroke-width="1.3"><rect x="4" y="1.5" width="6" height="11" rx="1"/><line x1="6" y1="10.5" x2="8" y2="10.5"/></svg>
    </li>
    <li>555-492-3071
      <svg viewBox="0 0 14 14" fill="none" stroke="#e0141e" stroke-width="1.3"><rect x="2" y="5" width="10" height="6" rx="1"/><rect x="4" y="2" width="6" height="3"/><rect x="4" y="9" width="6" height="3"/></svg>
    </li>
    <li>dwhitfield@lumo8.com
      <svg viewBox="0 0 14 14" fill="none" stroke="#e0141e" stroke-width="1.3"><rect x="1.5" y="3" width="11" height="8"/><path d="M1.5 3l5.5 5 5.5-5"/></svg>
    </li>
  </ul>

  <svg class="footer-band" viewBox="0 0 630 46" preserveAspectRatio="none" aria-hidden="true">
    <polygon points="0,0 248,0 262,40 630,40 630,46 0,46" fill="#e0141e"/>
    <polygon points="0,0 248,0 262,40 0,40" fill="#14295a"/>
  </svg>
  <div class="website">www.lumo8.com</div>
</section>

</body>
</html>
```